Vale Linebacker Needs a new website!

We need a four page website for a new company based in San Francisco. We help companies connect better with their clients, employees, and vendors by implementing collaborative technology.
Similar Websites
Mist Rangers - http://www.mistrangers.example/
Skyforthing - http://www.skyforthing.example/ - I don't like the the rotating window or the pictures of people. I like the icons used to go to the next pages.
Color Combos
Blues and Yellows - http://www.huepairings.example/palette-sets/96/HuePairing96.html
We prefer graphics over the actual pictures of people in the header. Pictures of people working together in the text is fine.
Web Page Layout
Index
Cloud Advisory Services
Email Everywhere
CRM Implementation
For detailed copy please see this link https://files.paperhold.example/a/widgetladyla.example/document/d/7KtmPzWqAeRbYcNvHsJgLdFxTuQoIeMnBvCxZaSdFgHj/edit
Industry/Entity Type
It Company

```html
<!DOCTYPE html>
<html lang="en">
<head>
<meta charset="utf-8">
<title>Vale Linebacker</title>
<link href="https://fonts.googleapis.com/css2?family=Open+Sans:ital,wght@0,400;0,600;0,700;1,600&display=swap" rel="stylesheet">
<style>
:root{
  --blue:#2565b5;
  --blue-dark:#1d55a0;
  --nav-top:#3a7fd6;
  --nav-bottom:#2462b4;
  --yellow:#f5c20f;
  --ink:#222;
  --muted:#444;
  --band:#f6f6f6;
  --rule:#e3e3e3;
  --footer:#4b4b4b;
  --footer-deep:#3b3b3b;
  --footer-text:#cfcfcf;
  --white:#fff;
}
*{box-sizing:border-box;margin:0;padding:0}
html,body{width:1200px;height:2356px;overflow:hidden;background:var(--white)}
body{position:relative;font-family:Arial,Helvetica,sans-serif;color:var(--ink)}
.abs{position:absolute}

/* header */
.brand{left:170px;top:46px;display:flex;align-items:center;gap:12px}
.brand-mark{width:30px;height:30px;border-radius:50%;background:var(--yellow)}
.brand-name{font-family:"Open Sans",sans-serif;font-weight:400;font-size:30px;color:var(--ink);line-height:1}
.search{left:843px;top:44px;width:186px;height:36px;border:1px solid #c9c9c9;border-radius:3px;box-shadow:inset 0 1px 2px rgba(0,0,0,.1);font-size:11px;font-style:italic;color:#999;padding:11px 12px}
.search svg{position:absolute;right:12px;top:9px}

/* nav */
.nav{left:0;top:123px;width:1200px;height:50px;background:linear-gradient(var(--nav-top),var(--nav-bottom))}
.nav-home{position:absolute;left:170px;top:0;width:81px;height:50px;background:var(--yellow);display:flex;align-items:center;justify-content:center}
.nav-item{position:absolute;top:17px;transform:translateX(-50%);font-family:"Open Sans",sans-serif;font-size:13px;color:var(--white);white-space:nowrap}

/* hero */
.hero{left:0;top:173px;width:1200px;height:518px;background:radial-gradient(ellipse at 50% 55%,#c9ced6 0%,#9ea4ad 55%,#7c828b 100%)}
.hero-device{left:432px;top:319px;width:366px;height:278px;border-radius:14px;background:linear-gradient(#f3f4f6,#dfe3e8);box-shadow:0 4px 16px rgba(0,0,0,.25)}
.hero-screen{left:460px;top:342px;width:310px;height:232px;background:linear-gradient(135deg,#b9d3ef,#e8edf3 60%,#cfd8e2)}
.hero-title{left:0;top:196px;width:1200px;text-align:center;font-family:"Open Sans",sans-serif;font-weight:400;font-size:38px;color:var(--white)}
.hero-sub{left:0;top:262px;width:1200px;text-align:center;font-size:12px;color:#333}
.hero-arrow{width:42px;height:42px;border-radius:50%;background:rgba(40,40,40,.6);display:flex;align-items:center;justify-content:center;top:381px}
.hero-arrow span{width:28px;height:28px;border-radius:50%;background:#eee;display:flex;align-items:center;justify-content:center}

/* sections */
.sec-title{left:0;width:1200px;text-align:center;font-family:"Open Sans",sans-serif}
.welcome{top:710px;font-size:28px;font-weight:400;color:#111}
.welcome b{font-weight:400;color:var(--blue)}
.lede{left:176px;width:850px;text-align:center;font-size:10.5px;line-height:20px;color:var(--muted)}
.feature{width:280px;text-align:center;transform:translateX(-50%)}
.feature-icon{width:126px;height:126px;margin:0 auto;border-radius:50%;background:#fff;border:2px solid #e5e5e5;display:flex;align-items:center;justify-content:center;position:relative}
.feature-icon::after{content:"";position:absolute;bottom:-9px;left:55px;border-left:8px solid transparent;border-right:8px solid transparent;border-top:10px solid var(--blue)}
.feature-icon i{width:112px;height:112px;border-radius:50%;background:var(--blue);display:flex;align-items:center;justify-content:center}
.feature h3{font-family:"Open Sans",sans-serif;font-weight:400;font-size:16.5px;color:#111;margin-top:21px}
.feature p{font-family:"Open Sans",sans-serif;font-size:10.5px;line-height:19.5px;color:#333;margin-top:17px;height:58px;overflow:hidden}

.band{left:0;top:1128px;width:1200px;height:415px;background:var(--band);border-top:1px solid var(--rule);border-bottom:1px solid var(--rule)}
.blue-head{font-size:26px;font-style:italic;font-weight:600;color:var(--blue)}
.intro{left:240px;width:720px;text-align:center;font-family:"Open Sans",sans-serif;font-style:italic;font-size:11.5px;line-height:20px;color:#333}
.service{width:280px;text-align:center;transform:translateX(-50%)}
.service-icon{width:110px;height:110px;margin:0 auto;border-radius:50%;background:#fff;border:2px solid #e3e3e3;display:flex;align-items:center;justify-content:center}
.service-icon i{width:98px;height:98px;border-radius:50%;background:var(--blue);display:flex;align-items:center;justify-content:center}
.service h3{font-family:"Open Sans",sans-serif;font-weight:400;font-size:16.5px;color:#111;margin-top:18px}
.service p{width:258px;margin:12px auto 0;font-size:10.5px;line-height:20px;color:#222}

/* news */
.news-card{top:1678px;width:267px;height:295px;border:1px solid #e2e2e2;border-radius:3px;background:#fff;box-shadow:0 1px 3px rgba(0,0,0,.06)}
.news-media{position:absolute;left:9px;top:9px;width:249px;height:159px}
.news-date{position:absolute;right:9px;top:133px;width:62px;height:35px;background:var(--blue);color:#fff;font-size:12px;display:flex;align-items:center;justify-content:center}
.news-card h4{position:absolute;left:9px;top:184px;font-family:"Open Sans",sans-serif;font-weight:400;font-size:16px;color:#111}
.news-card p{position:absolute;left:9px;top:218px;width:250px;font-size:10.5px;line-height:19px;color:#222}

/* partners */
.partners{left:0;top:2023px;width:1200px;height:90px;border-top:1px solid var(--rule);display:flex;justify-content:center;align-items:center;gap:74px}
.partner-badge{width:110px;height:30px;border-radius:4px;background:#e2e2e2}

/* footer */
.footer{left:0;top:2113px;width:1200px;height:184px;background:var(--footer)}
.f-col{position:absolute;top:33px}
.f-col h5{font-family:"Open Sans",sans-serif;font-weight:400;font-size:15.5px;color:#e4e4e4;margin-bottom:12px;letter-spacing:.3px}
.f-col a{display:block;font-size:10.5px;color:var(--footer-text);text-decoration:none;line-height:25px}
.f-col .note{font-family:Arial,sans-serif;font-size:10px;line-height:19px;color:#a9a9a9;width:268px}
.signup{position:absolute;left:767px;top:113px;display:flex}
.signup span{width:188px;height:42px;background:#fff;font-size:10.5px;color:#333;padding:14px 14px}
.signup b{width:75px;height:42px;background:var(--blue);color:#fff;font-family:"Open Sans",sans-serif;font-weight:400;font-size:15.5px;display:flex;align-items:center;justify-content:center}

.bottom{left:0;top:2297px;width:1200px;height:59px;background:var(--footer-deep)}
.social{position:absolute;left:173px;top:19px;display:flex;gap:7px}
.social i{width:20px;height:20px;border-radius:50%;background:#7d8ea6}
.copyright{position:absolute;right:170px;top:22px;font-size:11px;color:#ddd}
</style>
</head>
<body>

<header>
  <div class="abs brand">
    <span class="brand-mark"></span>
    <span class="brand-name">Vale Linebacker</span>
  </div>
  <div class="abs search">Search
    <svg width="18" height="18" viewBox="0 0 18 18"><circle cx="7" cy="7" r="5" fill="none" stroke="#2565b5" stroke-width="2.2"/><line x1="10.5" y1="10.5" x2="16" y2="16" stroke="#2565b5" stroke-width="3" stroke-linecap="round"/></svg>
  </div>
</header>

<nav class="abs nav">
  <div class="nav-home">
    <svg width="26" height="22" viewBox="0 0 26 22"><path d="M13 1 1 12h4v9h6v-6h4v6h6v-9h4z" fill="#fff"/></svg>
  </div>
  <span class="nav-item" style="left:308px">Company</span>
  <span class="nav-item" style="left:424px">Cloud Services</span>
  <span class="nav-item" style="left:551px">Cloud Advisory</span>
  <span class="nav-item" style="left:683px">Cloud Technology</span>
  <span class="nav-item" style="left:801px">Events</span>
  <span class="nav-item" style="left:898px">Partners</span>
  <span class="nav-item" style="left:983px">Contact</span>
</nav>

<section>
  <div class="abs hero" role="img" aria-label="Blurred office backdrop with soft floating cloud shapes"></div>
  <div class="abs hero-device"></div>
  <div class="abs hero-screen" role="img" aria-label="Hands holding a tablet that shows a glossy blue cloud"></div>
  <h1 class="abs hero-title">Customer Relationship Management</h1>
  <p class="abs hero-sub">Duis autem vel eum iriure qui dolor est etiam in velit esse molestie consequat, vel illum dolore eu feugiat nulla facilisis at vero eros.</p>
  <div class="abs hero-arrow" style="left:76px"><span><svg width="10" height="12" viewBox="0 0 10 12"><path d="M7 1 2 6l5 5" fill="none" stroke="#444" stroke-width="2"/></svg></span></div>
  <div class="abs hero-arrow" style="left:1071px"><span><svg width="10" height="12" viewBox="0 0 10 12"><path d="M3 1l5 5-5 5" fill="none" stroke="#444" stroke-width="2"/></svg></span></div>
</section>

<section>
  <h2 class="abs sec-title welcome">Welcome To <b>Vale Linebacker</b></h2>
  <p class="abs lede" style="top:752px">Etiam quis mi ante. Donec iaculis ornare enim non dapibus. Vivamus ac nisi eros. Nam non commodo mi. Pellentesque habitant morbi tristique senectus et netus et malesuada fames ac turpis egestas.Etiam quis mi ante. Donec iaculis ornare enim non dapibus. Vivamus ac nisi eros. Nam non commodo mi. Pellentesque habitant morbi tristique senectus et netus et malesuada fames ac turpis egestas. Donec iaculis ornare enim non dapibus. Vivamus ac nisi eros. Nam non commodo mi.</p>

  <div class="abs feature" style="left:316px;top:852px">
    <div class="feature-icon"><i>
      <svg width="80" height="56" viewBox="0 0 80 56"><path d="M18 50a14 14 0 0 1-2-28 18 18 0 0 1 34-6 13 13 0 0 1 20 10 12 12 0 0 1-2 24z" fill="#eef3fa"/><circle cx="40" cy="26" r="7" fill="#222"/><path d="M27 46c0-9 6-13 13-13s13 4 13 13z" fill="#222"/><path d="M52 36h8M56 32v8" stroke="#222" stroke-width="3"/></svg>
    </i></div>
    <h3>Cloud Advisory Services</h3>
    <p>Forward- thinking organizations would like to be more collaborative, flexible and productive. Put your cloud program on the path to success with our Advisory</p>
  </div>
  <div class="abs feature" style="left:609px;top:852px">
    <div class="feature-icon"><i>
      <svg width="64" height="46" viewBox="0 0 64 46"><rect x="2" y="2" width="60" height="42" fill="none" stroke="#fff" stroke-width="3.5"/><path d="M2 2l30 24L62 2M2 44l22-20M62 44 40 24" fill="none" stroke="#fff" stroke-width="3.5"/></svg>
    </i></div>
    <h3>Email Everywhere</h3>
    <p>Drive forward your business with innovative solutions for the enterprise with either Searchwell Apps or Deskhub 365.&nbsp; Experience improved collaboration, security,</p>
  </div>
  <div class="abs feature" style="left:902px;top:852px">
    <div class="feature-icon"><i>
      <svg width="56" height="56" viewBox="0 0 56 56"><path d="M30 8H6v42h42V26" fill="none" stroke="#fff" stroke-width="4.5"/><path d="M44 4l8 8-22 22-11 3 3-11z" fill="#fff"/></svg>
    </i></div>
    <h3>CRM Implementation</h3>
    <p>CRMs (Customer Relationship Management) can be complex and slow for employees to adopt.&nbsp; Accelerate your CRM adoption&nbsp; by selecting the right simple solu-</p>
  </div>
</section>

<section>
  <div class="abs band"></div>
  <h2 class="abs sec-title blue-head" style="top:1150px">WHAT WE DO</h2>
  <p class="abs intro" style="top:1200px">We challenge the status quo by providing unique insights, emerging strategies and proven best practices. Our unwavering focus is on customer satisfaction.&nbsp; Our services include:</p>

  <div class="abs service" style="left:308px;top:1279px">
    <div class="service-icon"><i>
      <svg width="50" height="46" viewBox="0 0 50 46"><rect x="2" y="22" width="10" height="22" fill="#fff"/><rect x="15" y="14" width="10" height="30" fill="#fff"/><rect x="28" y="24" width="8" height="20" fill="#fff"/><rect x="38" y="4" width="10" height="40" fill="#fff"/><path d="M4 16 20 6l12 10L46 2" fill="none" stroke="#fff" stroke-width="3"/></svg>
    </i></div>
    <h3>Implementation</h3>
    <p>Duis autem vel eum iriure qui dolor est etiam in velit esse molestie consequat, vel illum dolore eu feugiat nulla facilisis at vero eros.</p>
  </div>
  <div class="abs service" style="left:605px;top:1279px">
    <div class="service-icon"><i>
      <svg width="60" height="60" viewBox="0 0 60 60" fill="#fff" stroke="#fff" stroke-width="2.5"><circle cx="30" cy="30" r="8"/><line x1="30" y1="30" x2="30" y2="6"/><line x1="30" y1="30" x2="30" y2="54"/><line x1="30" y1="30" x2="6" y2="30"/><line x1="30" y1="30" x2="54" y2="30"/><line x1="30" y1="30" x2="13" y2="13"/><line x1="30" y1="30" x2="47" y2="47"/><line x1="30" y1="30" x2="47" y2="13"/><line x1="30" y1="30" x2="13" y2="47"/><circle cx="30" cy="6" r="4"/><circle cx="30" cy="54" r="4"/><circle cx="6" cy="30" r="4"/><circle cx="54" cy="30" r="4"/><circle cx="13" cy="13" r="4"/><circle cx="47" cy="47" r="4"/><circle cx="47" cy="13" r="4"/><circle cx="13" cy="47" r="4"/></svg>
    </i></div>
    <h3>Integration</h3>
    <p>Duis autem vel eum iriure qui dolor est etiam in velit esse molestie consequat, vel illum dolore eu feugiat nulla facilisis at vero eros.</p>
  </div>
  <div class="abs service" style="left:906px;top:1279px">
    <div class="service-icon"><i>
      <svg width="60" height="60" viewBox="0 0 60 60"><circle cx="22" cy="34" r="13" fill="none" stroke="#fff" stroke-width="8" stroke-dasharray="5 3.5"/><circle cx="22" cy="34" r="9" fill="#fff"/><circle cx="22" cy="34" r="4" fill="#2565b5"/><circle cx="44" cy="16" r="8" fill="none" stroke="#fff" stroke-width="6" stroke-dasharray="4 2.5"/><circle cx="44" cy="16" r="5" fill="#fff"/><circle cx="44" cy="16" r="2.5" fill="#2565b5"/><circle cx="46" cy="46" r="7" fill="none" stroke="#fff" stroke-width="5" stroke-dasharray="3.5 2.5"/><circle cx="46" cy="46" r="4" fill="#fff"/></svg>
    </i></div>
    <h3>Strategy</h3>
    <p>Duis autem vel eum iriure qui dolor est etiam in velit esse molestie consequat, vel illum dolore eu feugiat nulla facilisis at vero eros.</p>
  </div>
</section>

<section>
  <h2 class="abs sec-title blue-head" style="top:1562px">RECENT NEWS</h2>
  <p class="abs lede" style="top:1608px">Etiam quis mi ante. Donec iaculis ornare enim non dapibus. Vivamus ac nisi eros. Nam non commodo mi. Pellentesque habitant morbi tristique senectus et netus et malesuada fames ac turpis egestas.Etiam quis mi ante. Donec iaculis ornare enim non dapibus. Vivamus ac nisi eros. Nam non commodo mi. Pellentesque</p>

  <article class="abs news-card" style="left:173px">
    <div class="news-media" role="img" aria-label="Hand touching a glowing concept diagram" style="background:linear-gradient(135deg,#dfe9f3,#9ab8d6)"></div>
    <span class="news-date">27 FEB</span>
    <h4>Lorem ipsum dolor sit amet</h4>
    <p>Etiam quis mi ante. Donec iaculis ornare enim non dapibus. Vivamus ac nisi eros. Nam non commodo mi. Pellentesque habitant morbi tristique</p>
  </article>
  <article class="abs news-card" style="left:468px">
    <div class="news-media" role="img" aria-label="Open hands holding a small blue cloud" style="background:radial-gradient(circle at 50% 50%,#c9d9ea,#d9a688 75%,#e9ece8)"></div>
    <span class="news-date">27 FEB</span>
    <h4>Lorem ipsum dolor sit amet</h4>
    <p>Etiam quis mi ante. Donec iaculis ornare enim non dapibus. Vivamus ac nisi eros. Nam non commodo mi. Pellentesque habitant morbi tristique</p>
  </article>
  <article class="abs news-card" style="left:762px">
    <div class="news-media" role="img" aria-label="Tablets and phones floating among clouds in a blue sky" style="background:linear-gradient(#3f7fcf,#a9c8ea 55%,#eef3f8)"></div>
    <span class="news-date">27 FEB</span>
    <h4>Lorem ipsum dolor sit amet</h4>
    <p>Etiam quis mi ante. Donec iaculis ornare enim non dapibus. Vivamus ac nisi eros. Nam non commodo mi. Pellentesque habitant morbi tristique</p>
  </article>
</section>

<section class="abs partners" aria-label="Partners">
  <span class="partner-badge"></span>
  <span class="partner-badge"></span>
  <span class="partner-badge"></span>
  <span class="partner-badge"></span>
  <span class="partner-badge"></span>
</section>

<footer>
  <div class="abs footer">
    <div class="f-col" style="left:173px">
      <h5>CLOUD SERVICES</h5>
      <a href="#">Tallyforce</a><a href="#">Searchwell</a><a href="#">TicketHour</a>
    </div>
    <div class="f-col" style="left:371px">
      <h5>CLOUD ADVISORY</h5>
      <a href="#">CRM Advisory Services</a><a href="#">Productivity &amp; Collaboration</a><a href="#">Advisory Services</a><a href="#">Workshops</a>
    </div>
    <div class="f-col" style="left:592px">
      <h5>RESOURCES</h5>
      <a href="#">Videos</a><a href="#">White Papers</a><a href="#">Webinars</a>
    </div>
    <div class="f-col" style="left:767px">
      <h5>NEWSLETTER</h5>
      <p class="note">Excepteur sint occaecat cupidatat non proident, sunt in culpa qui officia deserunt mollit anim id est laborum.</p>
    </div>
    <div class="signup"><span>Enter Email</span><b>Sign Up</b></div>
  </div>
  <div class="abs bottom">
    <div class="social"><i></i><i></i><i></i><i></i><i></i><i></i></div>
    <p class="copyright">Copyright@2014 Vale Linebacker. All Right Reserved</p>
  </div>
</footer>

</body>
</html>
```